WordPress Design for both website and landing page for an expert

I need a clean and stylish design for my new website. I work as an expert (see attached file WHY HOW WHAT), my product is expert opinion (reports) for company evaluations You can use all of the attached pictures colored or black / white. The person is me, you can add other pictures, if you want. The design should be clean and stylish, so you could use white, black, gray, silver and / or one additional color. I have added an idea about my website, see attached file CONCEPT WEBSITE If you have any more information, please do not hesitate to contact us 'Hesitate to ask me ...

```html
<!DOCTYPE html>
<html lang="de">
<head>
<meta charset="utf-8">
<title>Aldo Brenner – Sachverständiger für Firmenbewertungen</title>
<link href="https://fonts.googleapis.com/css2?family=Montserrat:wght@400;500;600;700&family=Open+Sans:ital,wght@0,400;0,600;1,600;1,700&display=swap" rel="stylesheet">
<style>
:root{
  --blue:#3a66c4;
  --blue-dark:#2c52a8;
  --ink:#2b2b2b;
  --text:#6f6f6f;
  --muted:#9a9a9a;
  --line:#e4e6ea;
  --topbar:#3b3d40;
  --footer:#2e3033;
  --white:#ffffff;
  --soft:#f4f5f7;
}
*{box-sizing:border-box;margin:0;padding:0}
html,body{width:1200px;height:2632px;overflow:hidden}
body{font-family:"Open Sans",Arial,sans-serif;color:var(--text);background:var(--white);position:relative}
h1,h2,h3,.brand,.nav a,.btn{font-family:"Montserrat",Arial,sans-serif}

.topbar{height:48px;background:var(--topbar);color:#d6d6d6;font-size:14px;display:flex;align-items:center;padding:0 48px;gap:40px}
.topbar .lang{margin-right:auto}
.topbar span{display:flex;align-items:center;gap:8px}
.topbar svg{width:14px;height:14px;fill:#d6d6d6}

.header{height:92px;display:flex;align-items:center;padding:0 48px;background:var(--white)}
.brand{display:flex;align-items:center;gap:12px;color:var(--ink);font-weight:600;font-size:22px;letter-spacing:3px}
.brand i{width:26px;height:26px;border-radius:50%;background:var(--ink);display:block}
.nav{margin-left:auto;display:flex;gap:30px}
.nav a{color:#555;text-decoration:none;font-size:15px;font-weight:500}
.nav a.active{color:var(--ink);font-weight:700}

.hero{position:relative;height:520px;overflow:hidden}
.hero-photo{position:absolute;inset:0;background:linear-gradient(100deg,#f3f4f6 0%,#e4e7ea 45%,#b9bec5 70%,#6f757d 100%)}
.hero-text{position:absolute;left:64px;top:120px;width:560px}
.hero h1{font-family:"Open Sans",Arial,sans-serif;font-style:italic;font-weight:700;color:var(--blue);font-size:46px;line-height:54px}
.hero p{margin-top:14px;font-size:15px;color:var(--blue-dark);font-weight:600}
.hero .meta{margin-top:18px;display:flex;gap:34px;font-size:14px;color:#777}
.hero .meta span{display:flex;align-items:center;gap:8px}
.hero .meta svg{width:16px;height:16px;fill:#888}
.btn{display:inline-block;font-weight:600;font-size:15px;letter-spacing:1px;border-radius:30px;text-decoration:none}
.btn-solid{background:var(--blue);color:var(--white);padding:15px 40px;box-shadow:0 6px 14px rgba(58,102,196,.35)}
.hero .btn{position:absolute;left:64px;top:432px}
.hero-wave{position:absolute;left:0;bottom:0;width:1200px;height:110px}

.why{position:relative;height:600px}
.why-left{position:absolute;left:120px;top:80px;width:380px}
.eyebrow{color:var(--blue);font-weight:600;font-size:16px;letter-spacing:2px;font-family:"Montserrat",Arial,sans-serif}
.why h2{margin-top:14px;color:var(--ink);font-size:34px;font-weight:700;line-height:42px}
.why p{margin-top:22px;font-size:14px;line-height:24px}
.btn-outline{position:absolute;left:120px;top:458px;border:2px solid var(--blue);color:var(--blue);padding:12px 34px}
.card{position:absolute;background:var(--white);box-shadow:0 6px 24px rgba(0,0,0,.12);padding:22px 26px 22px 110px;width:420px}
.card h3{color:var(--blue);font-size:17px;font-weight:700}
.card p{font-size:13px;line-height:20px;margin-top:8px}
.badge{position:absolute;top:50%;transform:translateY(-50%);left:-42px;width:110px;height:110px;border-radius:50%;background:var(--blue);border:8px solid #dfe6f6;display:flex;align-items:center;justify-content:center}
.badge svg{width:38px;height:38px;fill:none;stroke:var(--white);stroke-width:2.2}
.card.c1{left:640px;top:90px}
.card.c2{left:560px;top:246px;padding:22px 110px 22px 26px}
.card.c2 .badge{left:auto;right:-42px}
.card.c3{left:660px;top:390px}

.faq{padding-top:120px;height:720px;border-top:1px solid var(--line);position:relative}
.faq h2{text-align:center;color:var(--ink);font-size:30px;font-weight:600}
.faq ul{list-style:none;width:968px;margin:48px auto 0}
.faq li{height:52px;border:1px solid var(--line);margin-bottom:12px;display:flex;align-items:center;padding:0 16px;font-size:14px;color:#555}
.faq li b{margin-left:auto;width:22px;height:22px;background:var(--blue);color:var(--white);font-size:16px;display:flex;align-items:center;justify-content:center;font-weight:600}
.faq .note{width:968px;margin:24px auto 0;font-size:14px;line-height:22px}

.promise{position:absolute;left:0;top:1880px;width:1200px;height:752px}
.promise svg.bg{position:absolute;inset:0}
.promise-text{position:absolute;top:128px;width:100%;text-align:center;color:var(--white)}
.promise h2{font-size:30px;font-weight:600;letter-spacing:1px}
.promise p{margin:22px auto 0;width:620px;font-size:15px;line-height:24px;color:#dbe4f7}
.btn-ghost{margin-top:32px;border:2px solid var(--white);color:var(--white);padding:13px 34px}

.footer{position:absolute;left:0;top:2280px;width:1200px;text-align:center;color:#bbb}
.footer .brand{justify-content:center;color:var(--white);margin-top:30px}
.footer .brand i{background:var(--white)}
.subscribe{margin:110px auto 0;width:600px;height:60px;background:var(--white);border-radius:30px;display:flex;align-items:center;padding:0 6px 0 28px}
.subscribe span{color:#999;font-size:15px}
.subscribe .btn{margin-left:auto;padding:14px 30px;font-size:14px}
.copy{margin-top:48px;font-size:13px}
</style>
</head>
<body>
<div class="topbar">
  <span class="lang">Lets Eng ▾</span>
  <span><svg viewBox="0 0 24 24"><path d="M12 2a7 7 0 0 0-7 7c0 5 7 13 7 13s7-8 7-13a7 7 0 0 0-7-7zm0 9.5A2.5 2.5 0 1 1 12 6.5a2.5 2.5 0 0 1 0 5z"/></svg>Brenner Büro, Musterstraße 12, DE</span>
  <span><svg viewBox="0 0 24 24"><path d="M6.6 10.8a15 15 0 0 0 6.6 6.6l2.2-2.2a1 1 0 0 1 1-.25 11 11 0 0 0 3.6.6 1 1 0 0 1 1 1V20a1 1 0 0 1-1 1A17 17 0 0 1 3 4a1 1 0 0 1 1-1h3.5a1 1 0 0 1 1 1 11 11 0 0 0 .6 3.6 1 1 0 0 1-.25 1z"/></svg>+1-555-010-2040</span>
  <span><svg viewBox="0 0 24 24"><path d="M3 5h18v14H3zm2 2v.5l7 4.5 7-4.5V7l-7 4.5z"/></svg>info@aldobrenner.de</span>
</div>

<header class="header">
  <div class="brand"><i></i>ALDO BRENNER</div>
  <nav class="nav">
    <a href="#" class="active">Home</a><a href="#">What I Do</a><a href="#">Why I Do It &amp; How I Do It</a><a href="#">About Me</a><a href="#">Contact</a>
  </nav>
</header>

<section class="hero">
  <div class="hero-photo" role="img" aria-label="Portrait photo of the expert in a dark suit on the right, bright office background"></div>
  <div class="hero-text">
    <h1>Sachverständiger<br>für Firmenbewertungen</h1>
    <p>Sie benötigen ein Gutachten zur Ermittlung des Wertes Ihres Unternehmens?</p>
    <div class="meta">
      <span><svg viewBox="0 0 24 24"><path d="M4 4h16v16H4zm2 2v12h12V6z"/></svg>Unser Ziel</span>
      <span><svg viewBox="0 0 24 24"><path d="M12 2l9 5v10l-9 5-9-5V7z"/></svg>Expert in Valuation</span>
    </div>
  </div>
  <a href="#" class="btn btn-solid">VIEW DETAILS</a>
  <svg class="hero-wave" viewBox="0 0 1200 110" preserveAspectRatio="none">
    <path d="M0 70 C300 20 700 120 1200 30 L1200 110 L0 110 Z" fill="#3a66c4"/>
    <path d="M0 86 C320 40 720 130 1200 52 L1200 110 L0 110 Z" fill="#ffffff"/>
  </svg>
</section>

<section class="why">
  <div class="why-left">
    <div class="eyebrow">_ ALDOBRENNER</div>
    <h2>WHY<br>CHOOSE US</h2>
    <p>Lorem ipsum dolor sit amet, consectetur adipiscing elit, sed do eiusmod tempor incididunt ut labore et dolore magna aliqua. Ut enim ad minim veniam, quis nostrud exercitat.</p>
    <p>Sed ut perspiciatis unde omnis iste natus error sit voluptatem accusantium doloremque laudantium totam rem aperiam, eaque ipsa quae ab illo inventore veritatis et quasi architecto beatae vitae dicta sunt explicabo.</p>
  </div>
  <a href="#" class="btn btn-outline">VIEW DETAILS</a>

  <div class="card c1">
    <div class="badge"><svg viewBox="0 0 24 24"><circle cx="12" cy="13" r="8"/><path d="M12 9v4l3 2M10 2h4"/></svg></div>
    <h3>1. SCHNELL</h3>
    <p>Sie bekommen Ihr Gutachten zeitnah innerhalb von nur 21 Tagen nach Zugang aller benötigten Unterlagen.</p>
  </div>
  <div class="card c2">
    <div class="badge"><svg viewBox="0 0 24 24"><circle cx="12" cy="9" r="6"/><path d="M8 14l-2 8 6-3 6 3-2-8"/></svg></div>
    <h3>2. ZERTIFIZIERT</h3>
    <p>Sie erhalten ein qualifiziertes und belastbares Gutachten von einem zertifizierten Sachverständigen durch die Akzeptanz bei allen Parteien.</p>
  </div>
  <div class="card c3">
    <div class="badge"><svg viewBox="0 0 24 24"><circle cx="9" cy="8" r="3.5"/><path d="M3 20c0-4 3-6 6-6s6 2 6 6M16 5a3 3 0 0 1 0 6M18 14c2 1 3 3 3 6"/></svg></div>
    <h3>3. VERSTÄNDLICH</h3>
    <p>Ihr Gutachten wird für Sie logisch und nachvollziehbar sein, ohne unnötige Fachchinesisch zu verwenden.</p>
  </div>
</section>

<section class="faq">
  <h2>FREQUENTLY ASKED QUESTIONS</h2>
  <ul>
    <li>Sie wollen Ihr Unternehmen auf Ihre Erben übertragen und benötigen eine Bewertung für das Finanzamt?<b>+</b></li>
    <li>Sie wollen Anteile Ihres Unternehmens oder Ihr gesamtes Unternehmen verkaufen?<b>+</b></li>
    <li>Was sind die Kaufmotive der Käufer?<b>+</b></li>
    <li>What are the buying motives of the customers?<b>+</b></li>
    <li>Sie müssen im Rahmen einer Trennung/Scheidung jemanden auszahlen und benötigen eine Bemessungsgrundlage?<b>+</b></li>
  </ul>
  <p class="note">Lassen Sie Ihr Unternehmen von einem qualifizierten Sachverständigen bewerten und gehen somit keine zusätzlichen Risiken ein. Die Kosten für ein Gutachten sind immer überschaubar und im Verhältnis zur Entscheidung gering.</p>
</section>

<section class="promise">
  <svg class="bg" viewBox="0 0 1200 752" preserveAspectRatio="none">
    <path d="M0 60 C300 0 800 0 1200 50 L1200 752 L0 752 Z" fill="#3a66c4"/>
    <path d="M0 440 C400 360 800 420 1200 380 L1200 752 L0 752 Z" fill="#2e3033"/>
  </svg>
  <div class="promise-text">
    <h2>MEIN QUALITÄTSVERSPRECHEN</h2>
    <p>Sollte der zwischen uns vereinbarte Termin für die Erstellung des Gutachtens überschritten werden, erhalten Sie das Gutachten kostenfrei.</p>
    <a href="#" class="btn btn-ghost">ICH VERZICHTE AUF MEIN HONORAR</a>
  </div>
</section>

<footer class="footer">
  <div class="brand"><i></i>ALDO BRENNER</div>
  <div class="subscribe"><span>Enter Your Email Address</span><a href="#" class="btn btn-solid">SUBSCRIBE NOW</a></div>
  <p class="copy">Copyright © 2018 All Rights Reserved | Terms of Use | Policy</p>
</footer>
</body>
</html>
```